Business card for medical clinic

I need an upmarket, modern medical/health business card for my clinic

Contact Information for Business Card

name, address, email, qr code

```html
<!DOCTYPE html>
<html lang="en">
<head>
<meta charset="utf-8">
<title>Meridia Care Clinic – Business Card</title>
<link rel="stylesheet" href="https://fonts.googleapis.com/css2?family=Montserrat:wght@400;500;700&display=swap">
<style>
  :root {
    --stage: #2b2b2d;
    --paper: #ffffff;
    --ink-dark: #141416;
    --brand-blue: #1d76aa;
    --bright-blue: #2aaee6;
    --deep-blue: #0e5a88;
    --text-light: #f4f6f8;
  }
  * { margin: 0; padding: 0; box-sizing: border-box; }
  html, body {
    width: 1200px; height: 880px; overflow: hidden;
    background: var(--stage);
    font-family: "Montserrat", sans-serif;
  }
  .stage { position: relative; width: 1200px; height: 880px; }

  .card {
    position: absolute;
    width: 640px; height: 366px;
    border-radius: 22px;
    background: var(--paper);
    overflow: hidden;
    box-shadow: 0 14px 30px rgba(0,0,0,0.45);
  }
  .card--front { left: 80px; top: 56px; }
  .card--back  { left: 480px; top: 460px; }

  .brand {
    position: absolute;
    display: flex; align-items: center; gap: 16px;
  }
  .brand__circle {
    width: 74px; height: 74px; border-radius: 50%;
    border: 6px solid var(--brand-blue);
    flex: none;
  }
  .brand__name {
    color: var(--brand-blue);
    font-weight: 500;
    letter-spacing: 0.06em;
    text-transform: uppercase;
    line-height: 1.15;
  }
  .card--front .brand { left: 110px; top: 140px; }
  .card--front .brand__name { font-size: 30px; }
  .card--back .brand { left: 40px; top: 60px; }
  .card--back .brand__circle { width: 56px; height: 56px; border-width: 5px; }
  .card--back .brand__name { font-size: 21px; }

  .back-panel { position: absolute; inset: 0; }

  .contact {
    position: absolute; right: 44px; top: 66px;
    text-align: right; color: var(--text-light);
  }
  .contact__name-row { display: flex; justify-content: flex-end; align-items: center; gap: 14px; }
  .contact__name {
    color: var(--bright-blue); font-weight: 700; font-size: 25px; letter-spacing: 0.02em;
  }
  .contact__bar { width: 14px; height: 40px; background: var(--bright-blue); }
  .contact__title { font-size: 15px; margin: 2px 28px 18px 0; }
  .contact__list { list-style: none; font-size: 15px; line-height: 1.55; }
  .contact__list li { display: flex; justify-content: flex-end; align-items: center; gap: 8px; }
  .contact__list svg { width: 13px; height: 13px; fill: var(--bright-blue); flex: none; }
  .contact__address { font-size: 15px; line-height: 1.45; margin-top: 14px; margin-right: 21px; }
</style>
</head>
<body>
<main class="stage">

  <section class="card card--front" aria-label="Card front">
    <div class="brand">
      <span class="brand__circle"></span>
      <span class="brand__name">Meridia Care<br>Clinic</span>
    </div>
  </section>

  <section class="card card--back" aria-label="Card back">
    <svg class="back-panel" viewBox="0 0 640 366" width="640" height="366" aria-hidden="true">
      <path d="M330,0 C440,40 420,150 385,230 C362,290 372,340 405,366 L640,366 L640,0 Z" fill="var(--ink-dark)"/>
      <path d="M352,8 C412,50 398,150 362,232 C338,292 348,336 376,358 C352,334 342,292 364,228 C392,150 400,58 352,8 Z" fill="var(--deep-blue)"/>
    </svg>

    <div class="brand">
      <span class="brand__circle"></span>
      <span class="brand__name">Meridia Care<br>Clinic</span>
    </div>

    <div class="contact">
      <div class="contact__name-row">
        <span class="contact__name">DANIEL HART</span>
        <span class="contact__bar"></span>
      </div>
      <p class="contact__title">Managing Director</p>
      <ul class="contact__list">
        <li>123 456 789
          <svg viewBox="0 0 16 16"><path d="M3 1h3l1.5 4-2 1.3a9 9 0 0 0 4.2 4.2L11 8.5l4 1.5v3a2 2 0 0 1-2 2A12 12 0 0 1 1 3a2 2 0 0 1 2-2z"/></svg>
        </li>
        <li>info@youremail.com
          <svg viewBox="0 0 16 16"><path d="M1 3h14v10H1z M1 3l7 6 7-6" stroke="#141416" stroke-width="1.2"/></svg>
        </li>
        <li>www.yourwebsite.com
          <svg viewBox="0 0 16 16"><circle cx="8" cy="8" r="7"/></svg>
        </li>
      </ul>
      <p class="contact__address">Your address, City<br>State, Zip 1234</p>
    </div>
  </section>

</main>
</body>
</html>
```